Company identity deisgn should support 2 languages

I would like to get our company identity design
This includes the following only
Business Cards 2 languages Arabic and English
Email signature
Letterhead
Linkedin profile images
Attached is the logo in Ai format

Requirements
Must have
• For business card
Must have
Name and Adrees in arabic
Name and Address in english
You might use both side of the card
Should not have
• Any pictures other than the logo

```html
<!DOCTYPE html>
<html lang="en">
<head>
<meta charset="utf-8">
<title>Nexora Logic — Business Cards</title>
<link rel="stylesheet" href="https://fonts.googleapis.com/css2?family=Poppins:wght@400;500&family=Cairo:wght@400;600&display=swap">
<style>
  :root {
    --brand-blue: #1877c2;
    --ink: #3c3c3c;
    --muted: #8d8d8d;
    --rule: #9a9a9a;
    --band-grey: #c4c4c6;
    --card: #ffffff;
    --backdrop: #e4e4e4;
  }
  * { box-sizing: border-box; margin: 0; padding: 0; }
  html, body { width: 1200px; height: 1200px; overflow: hidden; }
  body {
    background: var(--backdrop);
    font-family: "Poppins", sans-serif;
    color: var(--ink);
    position: relative;
  }
  .card {
    position: absolute;
    left: 257px;
    width: 686px;
    height: 392px;
    background: var(--card);
    border-radius: 26px;
    overflow: hidden;
    box-shadow: 0 10px 24px rgba(0,0,0,0.18);
  }
  .card--english { top: 165px; }
  .card--arabic { top: 653px; }

  .brand {
    position: absolute;
    right: 36px;
    top: 62px;
    display: flex;
    align-items: center;
    gap: 10px;
  }
  .brand__dot {
    width: 20px; height: 20px;
    border-radius: 50%;
    background: var(--brand-blue);
  }
  .brand__name {
    font-weight: 500;
    font-size: 22px;
    letter-spacing: 1px;
    color: var(--brand-blue);
  }

  .person {
    position: absolute;
    left: 38px;
    top: 196px;
  }
  .person__name {
    font-weight: 500;
    font-size: 23px;
    color: var(--brand-blue);
    line-height: 1.1;
  }
  .person__role {
    font-size: 15px;
    color: var(--muted);
    margin-top: 2px;
  }
  .card--arabic .person { top: 196px; }
  .card--arabic .person__name,
  .card--arabic .person__role {
    font-family: "Cairo", sans-serif;
  }
  .card--arabic .person__name { font-weight: 600; font-size: 23px; }
  .card--arabic .person__role { font-size: 16px; margin-top: -2px; }

  .divider {
    position: absolute;
    left: 39px;
    right: 36px;
    top: 259px;
    height: 1.5px;
    background: var(--rule);
  }
  .card--arabic .divider { right: 46px; height: 1px; background: #c2c2c2; }

  .contacts {
    position: absolute;
    left: 39px;
    top: 274px;
    list-style: none;
    font-size: 16px;
    line-height: 19.5px;
  }
  .contacts li { display: flex; align-items: center; gap: 8px; }
  .contacts svg { width: 13px; height: 13px; fill: var(--brand-blue); flex: none; }

  .address {
    position: absolute;
    right: 37px;
    bottom: 40px;
    text-align: right;
    font-size: 16px;
    line-height: 20px;
  }
  .address__web { margin-top: 2px; }
  .card--arabic .address { line-height: 24px; }
  .address__ar { font-family: "Cairo", sans-serif; font-size: 15px; }

  .band {
    position: absolute;
    left: 0; bottom: 0;
    width: 686px; height: 11px;
  }
</style>
</head>
<body>

<svg width="0" height="0" style="position:absolute" aria-hidden="true">
  <symbol id="icon-phone" viewBox="0 0 16 16">
    <path d="M3.2 1.2l2.3 2.6c.4.4.3 1-.1 1.4L4.3 6.3c.9 2 2.5 3.6 4.5 4.5l1.1-1.1c.4-.4 1-.4 1.4-.1l2.6 2.3c.4.4.4 1 0 1.4l-1.2 1.3c-.6.6-1.5.7-2.3.4C6 13.4 2.6 10 1 5.6.7 4.8.9 3.9 1.5 3.3L2.8 1.2c.1-.2.3-.2.4 0z"/>
  </symbol>
  <symbol id="icon-mobile" viewBox="0 0 16 16">
    <path d="M4 1h8a1 1 0 011 1v12a1 1 0 01-1 1H4a1 1 0 01-1-1V2a1 1 0 011-1zm1 2v9h6V3H5zm3 10a.8.8 0 100 1.6A.8.8 0 008 13z"/>
  </symbol>
  <symbol id="icon-fax" viewBox="0 0 16 16">
    <path d="M4 1h6l2 2v3H4V1zM1 7h14v6h-2v-2H3v2H1V7zm3 5h8v3H4v-3z"/>
  </symbol>
  <symbol id="icon-mail" viewBox="0 0 16 16">
    <path d="M1 3h14v10H1V3zm1.5 1.5v.3L8 9l5.5-4.2v-.3h-11zm0 2.2v4.8h11V6.7L8 11 2.5 6.7z"/>
  </symbol>
</svg>

<section class="card card--english" aria-label="Business card, English side">
  <div class="brand"><span class="brand__dot"></span><span class="brand__name">NEXORA LOGIC</span></div>
  <div class="person">
    <div class="person__name">DANIEL REYES</div>
    <div class="person__role">President</div>
  </div>
  <div class="divider"></div>
  <ul class="contacts">
    <li><svg><use href="#icon-phone"/></svg>412-308-1147</li>
    <li><svg><use href="#icon-mobile"/></svg>412-774-2093</li>
    <li><svg><use href="#icon-fax"/></svg>412-556-8810</li>
    <li><svg><use href="#icon-mail"/></svg>hello@nexoralogic.com</li>
  </ul>
  <div class="address">
    <div>4120 Willow Crest Drive</div>
    <div>Fairbanks, Alaska 99701</div>
    <div class="address__web">www.nexoralogic.com</div>
  </div>
  <svg class="band" viewBox="0 0 686 11" preserveAspectRatio="none" aria-hidden="true">
    <polygon points="0,0 404,0 401,11 0,11" fill="#1877c2"/>
    <polygon points="408,0 686,0 686,11 405,11" fill="#c4c4c6"/>
  </svg>
</section>

<section class="card card--arabic" aria-label="Business card, Arabic side">
  <div class="brand"><span class="brand__dot"></span><span class="brand__name">NEXORA LOGIC</span></div>
  <div class="person">
    <div class="person__name" dir="rtl" lang="ar">دانيال رييس</div>
    <div class="person__role" dir="rtl" lang="ar">رئيس</div>
  </div>
  <div class="divider"></div>
  <ul class="contacts">
    <li><svg><use href="#icon-phone"/></svg>412-308-1147</li>
    <li><svg><use href="#icon-mobile"/></svg>412-774-2093</li>
    <li><svg><use href="#icon-fax"/></svg>412-556-8810</li>
    <li><svg><use href="#icon-mail"/></svg>hello@nexoralogic.com</li>
  </ul>
  <div class="address">
    <div class="address__ar" dir="rtl" lang="ar">4120 ويلو كرست</div>
    <div class="address__ar" dir="rtl" lang="ar">فيربانكس، ألاسكا 99701</div>
    <div class="address__web">nexoralogic.com</div>
  </div>
  <svg class="band" viewBox="0 0 686 11" preserveAspectRatio="none" aria-hidden="true">
    <polygon points="0,0 413,0 410,11 0,11" fill="#1877c2"/>
    <polygon points="417,0 686,0 686,11 414,11" fill="#c4c4c6"/>
  </svg>
</section>

</body>
</html>
```